Torvel’s letterhead for local government

I require a letterhead for quarterly communications with constituents. The colours I have used in the past are navy & green (together) so I’m happy to use similar colours for this. Please refer to business card as an example.
The letter must make reference to the position I hold which is as per below
“Clr Torvel Quennisbury OAM”
And the tag line I have used in the past is “Torvel on the Terrace”. Although I’m not sure if this would be used in a letterhead or not. Happy for this to be provided as an option.
I would like a photo in the letterhead as I believe face recognition is key as an elected member.

Target Market(s)

Political interests

Industry/Entity Type

Government Office

Font styles to use
Sans Serif

Requirements
Must have
• Politically professional. I have been an elected member for 2 years so it is expected that the letterhead conveys that. The colours of the business card is to be used.
Nice to have
• Background of photos to be manipulated or changed to make me stand out, if possible?
Should not have
• Looked like it’s cropped or undertaken by an amateur designer.

```html
<!DOCTYPE html>
<html lang="en">
<head>
<meta charset="utf-8">
<title>Torvel Quennisbury Letterhead</title>
<link href="https://fonts.googleapis.com/css2?family=Arimo:wght@400;700&family=Open+Sans:wght@400;600&display=swap" rel="stylesheet">
<style>
  :root {
    --navy: #2a5d8f;
    --green: #44b669;
    --ink: #444444;
    --ink-strong: #2e2e2e;
    --paper: #ffffff;
    --portrait-top: #3a6fa3;
    --portrait-bottom: #2d3b4d;
  }
  * { margin: 0; padding: 0; box-sizing: border-box; }
  html, body { width: 1040px; height: 1200px; overflow: hidden; background: var(--paper); }
  .letterhead { position: relative; width: 1040px; height: 1200px; background: var(--paper); font-family: "Open Sans", sans-serif; color: var(--ink); }

  .masthead { position: absolute; left: 0; top: 0; width: 1040px; height: 232px; background: var(--navy); }
  .portrait { position: absolute; left: 49px; top: 13px; width: 272px; height: 219px;
    background: linear-gradient(180deg, var(--portrait-top) 0%, var(--portrait-bottom) 100%);
    border-radius: 120px 120px 0 0; }
  .title-panel { position: absolute; left: 345px; top: 56px; width: 576px; height: 137px; background: var(--green);
    font-family: "Arimo", sans-serif; color: #fff; padding: 26px 0 0 41px; }
  .title-panel .name { font-size: 28px; font-weight: 700; letter-spacing: 0.2px; }
  .title-panel .role { font-size: 20px; line-height: 26px; margin-top: 12px; }

  .letter-body { position: absolute; left: 97px; top: 255px; width: 840px; font-size: 15.5px; line-height: 27px; }
  .issue-date { margin-bottom: 9px; }
  .recipient { line-height: 18px; margin-bottom: 52px; }
  .salutation { margin-bottom: 27px; }
  .letter-body p.copy { text-align: justify; hyphens: auto; margin-bottom: 27px; }
  .sign-off { margin-top: 52px; }
  .signatory { margin-top: 55px; font-size: 18.5px; font-weight: 600; color: var(--ink-strong); line-height: 24px; }
  .signatory-role { line-height: 24px; }

  .footer-rule { position: absolute; left: 0; top: 1133px; width: 1040px; height: 7px; background: var(--green); }
  .footer { position: absolute; left: 0; top: 1140px; width: 1040px; height: 60px; background: var(--navy);
    display: flex; justify-content: center; align-items: center; gap: 22px;
    font-family: "Arimo", sans-serif; color: #fff; font-size: 19px; }
  .contact { display: flex; align-items: center; gap: 6px; }
  .contact svg { width: 28px; height: 28px; }
</style>
</head>
<body>
<div class="letterhead">
  <header class="masthead">
    <div class="portrait" role="img" aria-label="Portrait photo of Clr Torvel Quennisbury in a dark suit and tie"></div>
    <div class="title-panel">
      <div class="name">Clr Torvel Quennisbury OAM</div>
      <div class="role">Candidate for Area Councillor<br>City of Harrowfield</div>
    </div>
  </header>

  <main class="letter-body">
    <p class="issue-date">Issuing Date: May 5, 2018</p>
    <p class="recipient">Name Of Employee Mr. XYZABC<br>Address of Employee<br>Address Line 2 etc..</p>
    <p class="salutation">Dear Mr.XYZABC</p>
    <p class="copy">Lorem Ipsum has been the industry's standard dummy text ever since the 1500s, when an unknown printer took a galley of type and scrambled it to make a type specimen book. It has survived not only five centuries, but also the leap into electronic typesetting, remaining essentially unchanged. It was popularised in the 1960s with the release of Transferline sheets containing Lorem Ipsum passages, and more recently with desktop publishing software like Quillset Layout including versions of Lorem Ipsum.</p>
    <p class="copy">Lorem Ipsum is simply dummy text of the printing and typesetting industry. Lorem Ipsum has been the industry's standard dummy text ever since the 1500s, when an unknown printer took a galley of type and scrambled it to make a type specimen book.</p>
    <p class="copy">It has survived not only five centuries, but also the leap into electronic typesetting, remaining essentially unchanged. It was popularised in the 1960s with the release of Transferline sheets containing Lorem IpsumIpsum passages.</p>
    <p class="sign-off">Yours Sincerely</p>
    <p class="signatory">Merrick Halloway</p>
    <p class="signatory-role">Managing Director</p>
  </main>

  <div class="footer-rule"></div>
  <footer class="footer">
    <span class="contact">
      <svg viewBox="0 0 28 28" aria-hidden="true"><circle cx="14" cy="14" r="12" fill="none" stroke="#fff" stroke-width="2"/><path d="M10 8.5c1-.6 1.8.3 2.3 1.5.4 1-.7 1.5-.6 2.2.2 1.3 2.4 3.6 3.7 3.8.7.1 1.2-1 2.2-.6 1.2.5 2.1 1.3 1.5 2.3-.7 1.2-2 1.6-3.4 1.1-3-1.1-6-4.1-6.9-7.1-.4-1.4 0-2.6 1.2-3.2z" fill="#fff"/></svg>
      055-987 321 640
    </span>
    <span class="contact">
      <svg viewBox="0 0 28 28" aria-hidden="true"><circle cx="14" cy="14" r="12" fill="none" stroke="#fff" stroke-width="2"/><rect x="7.5" y="9.5" width="13" height="9" rx="1" fill="#fff"/><path d="M8 10.5l6 4.5 6-4.5" fill="none" stroke="#2a5d8f" stroke-width="1.3"/></svg>
      hello@quennisbury.org
    </span>
    <span class="contact">
      <svg viewBox="0 0 28 28" aria-hidden="true"><circle cx="14" cy="14" r="12" fill="none" stroke="#fff" stroke-width="2"/><g fill="none" stroke="#fff" stroke-width="1.3"><circle cx="14" cy="14" r="6.5"/><ellipse cx="14" cy="14" rx="2.8" ry="6.5"/><path d="M7.5 14h13M8.5 10.8h11M8.5 17.2h11"/></g></svg>
      www.quennisbury.org
    </span>
  </footer>
</div>
</body>
</html>
```